Want to fly? Flight school needs a roll up

Hello designers

We are a small aviation club with around 100 members. We love flying and therefore offer free flight lessons for young people at our glider flight school.
The young people only have to pay a flat rate of €300 for the aircraft until their first solo flight.
To advertise the flight school we now need a roll up banner measuring 85cm x 200cm. You can find the data sheet for the banner in the appendix.
Content of the roll up banner:
Advertising for our flight school so that we can attract new members
The banner should be designed in our club colors blue/white
The banner is aimed at all people who want to get a glider license
A great offer for young people up to the age of 25 should be placed on the banner with a reference to the text “Offer only applies to people up to the age of 25. Included in the flat rate of €300 is training on the glider up to the first "solo flight"
The banner is intended to advertise training with a glider. Therefore the wish would be for a glider to be depicted

Here is a link to our current homepage

https://www.lgk-tarnholm.de/

https://www.vidoplex.example/watch?v=Qk7pL2xNz9c

Target Market(s)

Young people from 14 years to 30 years

Colors
0054AA
0677BA
7BADD7
CADEEF
E8F1F8

Requirements
Nice to have
• Glider / club logo
Should not have
• Too much text

```html
<!DOCTYPE html>
<html lang="en">
<head>
<meta charset="utf-8">
<title>Free Flight Lessons – Roll-up Banner</title>
<link rel="stylesheet" href="https://fonts.googleapis.com/css2?family=Anton&family=Oswald:wght@700&family=Poppins:wght@400;600;700;800&display=swap">
<style>
  :root {
    --club-blue: #1010b0;
    --deep-blue: #0a0a8c;
    --ink: #2b2b36;
    --sky: #7badd7;
    --sky-light: #cadeef;
    --mist: #e8f1f8;
    --text-grey: #3a3a3a;
    --white: #ffffff;
  }
  * { margin: 0; padding: 0; box-sizing: border-box; }
  html, body { width: 1200px; height: 2400px; overflow: hidden; background: #ffffff; }
  .banner {
    position: relative; width: 1200px; height: 2400px; overflow: hidden;
    background: var(--white); font-family: "Poppins", sans-serif;
  }
  .hero { position: absolute; left: 0; top: 0; }
  .club-mark {
    position: absolute; left: 130px; top: 580px; width: 370px;
    display: flex; flex-direction: column; align-items: center; gap: 20px;
  }
  .club-mark__dot { width: 150px; height: 150px; border-radius: 50%; background: var(--club-blue); }
  .club-mark__name {
    font-weight: 700; font-size: 30px; line-height: 1.25;
    color: var(--club-blue); text-align: center;
  }
  .lower-field {
    position: absolute; left: 0; top: 1465px; width: 1200px; height: 935px;
    background: linear-gradient(180deg, #f4f4f4 0%, #e2e2e2 45%, #c9c9c9 100%);
  }
  .headline-free {
    position: absolute; top: 940px; left: 0; width: 1200px; text-align: center;
    font-family: "Anton", sans-serif; font-weight: 400; font-size: 250px; line-height: 1; color: var(--ink);
    transform: scaleX(1.6); transform-origin: center;
  }
  .headline-lessons {
    position: absolute; top: 1160px; left: 0; width: 1200px; text-align: center;
    font-family: "Oswald", sans-serif; font-weight: 700; font-size: 142px; line-height: 1;
    color: var(--club-blue);
  }
  .ribbon { position: absolute; left: 90px; top: 1320px; }
  .ribbon__text {
    position: absolute; left: 90px; top: 1332px; width: 1060px; text-align: center;
    font-weight: 700; font-size: 50px; line-height: 58px; color: var(--white); letter-spacing: 2px;
  }
  .divider { position: absolute; top: 1500px; width: 2px; height: 300px; background: rgba(255,255,255,.85); }
  .discipline {
    position: absolute; top: 1512px; width: 340px; display: flex; flex-direction: column; align-items: center;
  }
  .discipline__photo {
    width: 220px; height: 220px; border-radius: 50%; border: 8px solid var(--club-blue);
    box-shadow: 0 0 0 5px var(--white);
  }
  .discipline__photo--cockpit { background: linear-gradient(160deg, #dfe6ea, #8d9aa3 60%, #f2f2f2); }
  .discipline__photo--motor { background: linear-gradient(180deg, #aabd7a 0%, #6f8a3f 60%, #55702e 100%); }
  .discipline__photo--powered { background: linear-gradient(180deg, #dfe8ee 0%, #c9d5dc 55%, #4f6a3a 75%, #6f7e45 100%); }
  .discipline__label {
    margin-top: 12px; font-weight: 700; font-size: 34px; line-height: 1.15; color: var(--text-grey); text-align: center;
  }
  .price {
    position: absolute; left: 110px; top: 1872px; font-weight: 800; font-size: 150px; line-height: 1;
    color: var(--club-blue); transform: scaleX(1.5); transform-origin: left center;
  }
  .price__currency { font-size: 72px; color: var(--ink); vertical-align: 58px; margin-right: 2px; }
  .price-note {
    position: absolute; left: 110px; top: 2035px; font-weight: 700; font-size: 40px; line-height: 45px; color: var(--text-grey);
  }
  .price-note__accent { color: var(--club-blue); }
  .age-badge {
    position: absolute; left: 740px; top: 1840px; width: 400px; height: 350px; border-radius: 50%;
    background: radial-gradient(circle at 50% 45%, #ffffff 55%, #dcdcf2 100%);
    border: 6px solid var(--white); box-shadow: 0 10px 24px rgba(0,0,0,.12);
    display: flex; flex-direction: column; align-items: center; justify-content: center; text-align: center;
  }
  .age-badge__text { font-weight: 400; font-size: 34px; line-height: 38px; color: #333; }
  .age-badge__age { font-weight: 800; font-size: 90px; line-height: 1; color: var(--club-blue); margin-top: 6px; }
  .footer { position: absolute; left: 0; top: 2150px; }
  .footer__url {
    position: absolute; left: 470px; top: 2292px; width: 650px; text-align: center;
    font-weight: 700; font-size: 40px; letter-spacing: 3px; color: var(--white);
  }
</style>
</head>
<body>
<main class="banner">
  <svg class="hero" width="1200" height="1010" viewBox="0 0 1200 1010">
    <defs>
      <linearGradient id="sky" x1="0" y1="0" x2="0" y2="1">
        <stop offset="0" stop-color="#4aa6e6"/>
        <stop offset="0.45" stop-color="#cadeef"/>
        <stop offset="0.7" stop-color="#8aa6bf"/>
        <stop offset="1" stop-color="#5c6a55"/>
      </linearGradient>
      <radialGradient id="blueglow" cx="0.4" cy="0.4" r="0.7">
        <stop offset="0" stop-color="#2a2ad0"/>
        <stop offset="1" stop-color="#0a0a8c"/>
      </radialGradient>
    </defs>
    <path d="M0 0 H610 C 610 330, 420 522, 140 522 C 80 522, 35 515, 0 505 Z" fill="var(--ink)"/>
    <path d="M0 0 H586 C 586 290, 400 460, 150 460 C 90 460, 40 452, 0 442 Z" fill="url(#blueglow)"/>
    <path d="M540 400 C 560 760, 880 980, 1200 998 L 1200 862 C 980 850, 700 760, 600 560 Z" fill="var(--club-blue)"/>
    <path role="img" aria-label="Photo of an aerobatic aircraft flying over rocky mountains under a blue sky"
          d="M586 0 H1200 V862 C 980 850, 700 760, 600 560 C 540 420, 600 200, 586 0 Z" fill="url(#sky)"/>
  </svg>

  <div class="club-mark">
    <span class="club-mark__dot"></span>
    <span class="club-mark__name">Luftgleitklub Tarnholm e.V.</span>
  </div>

  <div class="lower-field" role="img" aria-label="Faded background photo of an aircraft and airfield"></div>

  <h1 class="headline-free">FREE</h1>
  <h2 class="headline-lessons">FLIGHT LESSONS</h2>

  <svg class="ribbon" width="1060" height="140" viewBox="0 0 1060 140">
    <polygon points="20,0 1040,0 1000,70 1060,140 0,140 40,70" fill="var(--club-blue)"/>
  </svg>
  <p class="ribbon__text">FOR YOUNG PEOPLE AT<br>OUR GLIDER FLIGHT SCHOOL</p>

  <span class="divider" style="left:403px"></span>
  <span class="divider" style="left:787px"></span>

  <div class="discipline" style="left:52px">
    <div class="discipline__photo discipline__photo--cockpit" role="img" aria-label="Glider cockpit photo"></div>
    <p class="discipline__label">GLIDING</p>
  </div>
  <div class="discipline" style="left:425px">
    <div class="discipline__photo discipline__photo--motor" role="img" aria-label="Motor glider on a grass airfield photo"></div>
    <p class="discipline__label">MOTOR GLIDER</p>
  </div>
  <div class="discipline" style="left:808px">
    <div class="discipline__photo discipline__photo--powered" role="img" aria-label="Small powered aircraft taking off photo"></div>
    <p class="discipline__label">POWERED<br>FLIGHT</p>
  </div>

  <p class="price"><span class="price__currency">€</span>300</p>
  <p class="price-note">IS TRAINING ON THE<br>GLIDER UP TO THE FIRST<br><span class="price-note__accent">"SOLO FLIGHT"</span></p>

  <div class="age-badge">
    <p class="age-badge__text">Offer only<br>applies to<br>people up to<br>the age of</p>
    <p class="age-badge__age">25</p>
  </div>

  <svg class="footer" width="1200" height="250" viewBox="0 0 1200 250">
    <path d="M0 108 C 120 90, 250 95, 340 120 L 340 250 L 0 250 Z" fill="var(--ink)"/>
    <path d="M180 250 C 360 120, 700 55, 1200 60 V 250 Z" fill="var(--white)"/>
    <path d="M205 250 C 385 132, 720 72, 1200 76 V 250 Z" fill="var(--club-blue)"/>
  </svg>
  <p class="footer__url">www.lgk-tarnholm.de</p>
</main>
</body>
</html>
```